Business card design needed

I would like a one sided black business card with the information provided above. Refer to my website www.brightvolleyracquets.com.au for an example of colors I have used for my site, would like to keep this consistent for my business cards also, I will upload my logo below.

I am a new small business that provides tennis customers with racquet re stringing, tennis strings and accessories.

Industry/Entity Type

Small Business

Contact Information for Business Card

Bright Volley Tennis

Owen Whitby
Managing Director

brightvolleyracquets@mailbox.example
www.brightvolleyracquets.com.au
0491 726 305

Racquet Restringing/Tennis Strings/Accessories

Requirements
Must have
• Must have my logo and card must be black

```html
<!DOCTYPE html>
<html lang="en">
<head>
<meta charset="utf-8">
<title>Bright Volley Tennis – Business Card</title>
<link rel="stylesheet" href="https://fonts.googleapis.com/css2?family=Open+Sans:wght@400&display=swap">
<style>
  :root {
    --backdrop: #9a5b34;
    --card-black: #000000;
    --brand-lime: #b5d334;
    --brand-blue: #2e5088;
    --ink-dark: #111111;
    --ink-light: #ffffff;
  }
  * { margin: 0; padding: 0; box-sizing: border-box; }
  html, body {
    width: 1200px;
    height: 475px;
    overflow: hidden;
    background: var(--backdrop);
    font-family: "Open Sans", Arial, sans-serif;
    font-weight: 400;
  }
  .canvas {
    position: relative;
    width: 1200px;
    height: 475px;
  }
  .card {
    position: absolute;
    top: 81px;
    width: 547px;
    height: 312px;
    background: var(--card-black);
    overflow: hidden;
  }
  .card--front { left: 27px; }
  .card--back { left: 602px; }

  .card__swoosh {
    position: absolute;
    inset: 0;
    width: 100%;
    height: 100%;
  }
  .swoosh-blue { fill: var(--brand-blue); }
  .swoosh-lime { fill: var(--brand-lime); }

  .brand {
    position: absolute;
    display: flex;
    align-items: center;
    gap: 12px;
    color: var(--brand-lime);
    font-size: 28px;
    letter-spacing: 0.5px;
    text-transform: uppercase;
    white-space: nowrap;
  }
  .brand__dot {
    width: 30px;
    height: 30px;
    border-radius: 50%;
    background: var(--brand-lime);
    flex: none;
  }
  .card--front .brand { left: 36px; top: 92px; }
  .card--back .brand { left: 50%; top: 124px; transform: translateX(-50%); }

  .holder {
    position: absolute;
    left: 34px;
    top: 248px;
    color: var(--brand-lime);
  }
  .holder__name {
    font-size: 20px;
    line-height: 24px;
    text-transform: uppercase;
  }
  .holder__role {
    font-size: 13px;
    line-height: 18px;
  }

  .contacts {
    position: absolute;
    right: 16px;
    top: 247px;
    list-style: none;
    text-align: right;
    color: var(--ink-dark);
    font-size: 13px;
    line-height: 19px;
  }

  .card__web {
    position: absolute;
    left: 0;
    right: 0;
    top: 259px;
    text-align: center;
    color: var(--ink-light);
    font-size: 13px;
    letter-spacing: 2px;
  }
</style>
</head>
<body>
<main class="canvas">

  <section class="card card--front" aria-label="Business card front">
    <svg class="card__swoosh" viewBox="0 0 525 299" preserveAspectRatio="none" aria-hidden="true">
      <path class="swoosh-blue" d="M457,0 C500,90 430,210 159,299 L185,299 C340,265 470,160 525,30 L525,0 Z"/>
      <path class="swoosh-lime" d="M525,30 C470,160 340,265 185,299 L525,299 Z"/>
    </svg>

    <div class="brand">
      <span class="brand__dot" aria-hidden="true"></span>
      <span class="brand__name">Bright Volley Tennis</span>
    </div>

    <div class="holder">
      <p class="holder__name">Owen Whitby</p>
      <p class="holder__role">Managing Director</p>
    </div>

    <ul class="contacts">
      <li class="contacts__phone">P : 0491 726 305</li>
      <li class="contacts__email">E : brightvolleyracquets@mailbox.example</li>
      <li class="contacts__web">W: www.brightvolleyracquets.com.au</li>
    </ul>
  </section>

  <section class="card card--back" aria-label="Business card back">
    <div class="brand">
      <span class="brand__dot" aria-hidden="true"></span>
      <span class="brand__name">Bright Volley Tennis</span>
    </div>
    <p class="card__web">www.brightvolleyracquets.com.au</p>
  </section>

</main>
</body>
</html>
```